Homepage mockup for RoutineVerdict.com

I would like a homepage mockup of routineverdict.com.

Basically what the site does, is it allows a person to upload a video of a gymnastics routine and our certified judges will judge the routine providing a score, as well as provide a critique and feedback as to why they gave you that score. Many times people don't know why they got the score they did at a gymnastics competition, so this site aims to provide reasoning behind it.

I have started to design the homepage myself (see attached), and like it, but I'd like a professional to finish the layout, or even come up with something really wow and original. I like clean, typically simple design.

THIS IS AN OLD VERSION OF THE SITE (http://esite.kelpradia.com/) This should only be used so you can get an idea of what the site is about. I DO NOT want the new site to look like this, but the basic concept and content remains the same.

DESIGNER FILES CAN BE DOWNLOADED HERE (http://kelpradia.com/files.aspx)

Target Market(s)

Gymnastic type people, parents of gymnasts, coaches, etc.

Industry/Entity Type

It Professional

Requirements
Must have
• -Routine verdict logo (provided)
-Not required, but I have attached the main photo I used in my mockup (AI File)
*A step by step graphic(s) depicting the process for a user. A How it works sort of explanation. Should be eye catching, not just text.

-Step 1: Videotape your gymnastic routine.
-Step 2: Create an account and share us your video.
-Step 3: Our certified judges will score and critique your routine, fully explaining the reasons behind their score.

```html
<!DOCTYPE html>
<html lang="en">
<head>
<meta charset="utf-8">
<title>Routine verdict — Home</title>
<link rel="stylesheet" href="https://fonts.googleapis.com/css2?family=Ubuntu:wght@400;500;700&family=Yanone+Kaffeesatz:wght@300;400;600;700&display=swap">
<style>
:root{
  --blue-top:#4a78c4;
  --blue-bottom:#2a58a8;
  --blue-deep:#1e4a97;
  --red:#d01c1f;
  --red-dark:#a80f13;
  --ink:#1b1b1b;
  --heading-red:#a8101a;
  --panel:#ffffff;
  --panel-low:#f3f3f3;
  --footer:#2b2b2b;
  --beam:#d9b99a;
}
*{box-sizing:border-box;margin:0;padding:0}
html,body{width:1200px;height:1069px;overflow:hidden}
body{position:relative;background:#e9e9e9;font-family:'Ubuntu',sans-serif;color:var(--ink)}
.abs{position:absolute}

/* header */
.site-header{left:0;top:0;width:1200px;height:114px;background:linear-gradient(#4d7cc8,var(--blue-bottom));border-bottom:2px solid #dfe6f2}
.brand{left:147px;top:38px;display:flex;align-items:center;gap:10px;color:#fff;font-family:'Ubuntu',sans-serif;font-weight:700;font-size:34px;letter-spacing:-.5px}
.brand-mark{width:26px;height:26px;background:#fff;border-radius:50%}
.login label{position:absolute;top:26px;color:#fff;font-size:9px}
.login .field{position:absolute;top:20px;height:24px;background:#fff;border:2px solid #c9d6ea;border-radius:3px;font-size:8px;font-style:italic;color:#aaa;padding:5px 6px}
.btn-login{left:849px;top:20px;width:58px;height:25px;background:linear-gradient(#fff,#e4e4e4);border:2px solid #c9d6ea;border-radius:3px;font-size:13px;font-weight:500;text-align:center;line-height:21px;color:#333}
.btn-signup{left:923px;top:12px;width:131px;height:38px;background:linear-gradient(#fff,#e4e4e4);border:2px solid #c9d6ea;border-radius:3px;font-size:19px;font-weight:700;text-align:center;line-height:34px;color:#222}
.main-nav a{position:absolute;top:80px;color:#fff;text-decoration:none;font-family:'Yanone Kaffeesatz',sans-serif;font-size:17px;line-height:14px;text-align:center;transform:translateX(-50%)}
.main-nav a.single{top:88px}
.main-nav .active{left:582px;top:74px;width:70px;height:47px;transform:none;background:linear-gradient(#fff,#e9e9e9);color:#333;padding-top:15px}

/* hero */
.hero{left:0;top:116px;width:1200px;height:368px;background:linear-gradient(#e6e6e6,#fbfbfb 70%,#f3f0ec)}
.beam{left:0;top:446px;width:1200px;height:38px;background:linear-gradient(#efe3d6,var(--beam) 50%,#c79e7a);border-bottom:2px solid #b98a66}
.video{left:161px;top:158px;width:413px;height:251px;background:#111;border:1px solid #444;box-shadow:0 2px 4px rgba(0,0,0,.3)}
.video-frame{left:0;top:0;width:411px;height:214px;background:linear-gradient(135deg,#8a6a52,#b89070 40%,#5a6e8a 75%,#d27a3a)}
.play{left:160px;top:72px;width:80px;height:80px;border-radius:50%;background:rgba(40,40,40,.55)}
.controls{left:0;top:214px;width:411px;height:35px;background:linear-gradient(#2c2c2c,#111)}
.controls .time{position:absolute;left:233px;top:10px;color:#fff;font-size:12px}
.controls .time span{color:#888}
.controls .hd{position:absolute;left:385px;top:10px;color:#ddd;font-size:11px;font-weight:700;font-style:italic}
.gymnast{left:760px;top:177px;width:291px;height:297px;border-radius:40% 30% 20% 40%;background:radial-gradient(circle at 55% 45%,#d8b497,#e9ddd2 55%,rgba(240,236,232,0) 72%)}
.tagline{left:604px;top:153px;font-size:22px;line-height:28px;color:#222;z-index:2}
.tagline.second{top:265px;line-height:25px}
.cta{left:595px;top:361px;width:191px;height:48px;border-radius:12px;background:#c5c5c5;padding:4px;z-index:2}
.cta-inner{width:100%;height:100%;border-radius:9px;background:linear-gradient(#3c6cc0,#1d4592);display:flex;align-items:center;justify-content:center;gap:10px;color:#fff}
.cta-inner small{font-size:8px;line-height:9px;text-align:right;font-weight:500}
.cta-inner b{font-family:'Yanone Kaffeesatz',sans-serif;font-size:19px;font-weight:600}

/* content */
.panel{left:144px;top:505px;width:912px;height:511px;background:linear-gradient(var(--panel) 0,var(--panel) 213px,#e6e6e6 214px,var(--panel-low) 215px)}
.card{top:525px;width:277px;height:159px;background:linear-gradient(#e8272a,var(--red) 50%,var(--red-dark));border:2px solid #b0080d;border-radius:3px;overflow:hidden;color:#fff}
.card .icon{position:absolute;left:13px;top:21px;width:107px;height:107px;border-radius:50%;background:radial-gradient(#fff,#e4e4e4);border:3px solid #f0f0f0}
.card h3{position:absolute;left:128px;top:18px;font-family:'Yanone Kaffeesatz',sans-serif;font-weight:300;font-size:24px;line-height:26px;white-space:nowrap;letter-spacing:-.2px}
.card p{position:absolute;left:128px;top:79px;font-size:10px;line-height:13px;width:140px}
.card .more{position:absolute;left:151px;bottom:0;width:126px;height:33px;background:#2a2a2a;font-size:14px;line-height:31px;text-align:right;padding-right:22px}
.card .more::before{content:"";position:absolute;left:-16px;top:0;border-right:16px solid #2a2a2a;border-top:33px solid transparent}
.step{top:749px;width:279px;height:53px;background:linear-gradient(#5b86cf,var(--blue-deep));border:2px solid #c9d6ea;color:#fff;font-family:'Yanone Kaffeesatz',sans-serif;font-weight:700;font-size:29px;line-height:49px;text-shadow:0 1px 1px rgba(0,0,0,.3)}
.step .pic{position:absolute;left:20px;top:-8px;width:44px;height:60px;border-radius:10px;background:linear-gradient(#d9dde6,#7a869c)}
.step .label{position:absolute;left:97px;white-space:nowrap}
.step .qmark{position:absolute;left:22px;top:-10px;font-family:'Ubuntu',sans-serif;font-size:62px;line-height:66px;color:#e8e8e8}
.intro-title{left:165px;top:834px;font-size:22px;color:var(--heading-red);font-weight:400}
.intro-title b{font-weight:700}
.intro-copy{left:166px;top:876px;width:852px;font-size:11.6px;line-height:21.5px}

/* footer */
.site-footer{left:0;top:1016px;width:1200px;height:53px;background:var(--footer)}
.footer-nav{left:166px;top:1035px;font-size:10.5px;color:#ccc}
.footer-nav a{color:#ccc;text-decoration:none}
.footer-nav i{font-style:normal;margin:0 5px}
.copyright{right:164px;top:1035px;font-size:10.5px;color:#ccc}
</style>
</head>
<body>

<header class="abs site-header">
  <div class="abs brand"><span class="brand-mark"></span>Routine verdict</div>
  <form class="login">
    <label style="left:517px">Email:</label>
    <div class="field" style="left:545px;width:121px">enter your email</div>
    <label style="left:674px">Password:</label>
    <div class="field" style="left:721px;width:121px">enter your password</div>
  </form>
  <div class="abs btn-login">Login</div>
  <div class="abs btn-signup">Sign Up Now</div>
  <nav class="main-nav">
    <a class="active" href="#">Home</a>
    <a href="#" style="left:712px">How it<br>works</a>
    <a class="single" href="#" style="left:790px">FAQ</a>
    <a href="#" style="left:870px">Sample<br>critique</a>
    <a href="#" style="left:949px">Member<br>Area</a>
    <a class="single" href="#" style="left:1028px">About</a>
  </nav>
</header>

<section class="abs hero"></section>
<div class="abs beam"></div>
<div class="abs video">
  <div class="abs video-frame" role="img" aria-label="Video still of a group of smiling girls stretching in a gym"></div>
  <div class="abs play">
    <svg width="80" height="80"><polygon points="34,24 58,40 34,56" fill="#ddd"/></svg>
  </div>
  <div class="abs controls">
    <svg width="411" height="35">
      <polygon points="12,12 18,17 12,22" fill="#fff"/>
      <rect x="26" y="15" width="200" height="5" fill="#444"/>
      <rect x="26" y="15" width="84" height="5" fill="#d2141c"/>
      <polygon points="318,13 322,13 326,10 326,24 322,21 318,21" fill="#fff"/>
      <rect x="331" y="15" width="30" height="5" fill="#444"/>
      <rect x="331" y="15" width="22" height="5" fill="#d2141c"/>
      <line x1="369" y1="3" x2="369" y2="32" stroke="#333"/>
      <rect x="376" y="13" width="11" height="8" fill="none" stroke="#fff" stroke-width="1.5"/>
    </svg>
    <div class="time">1:26 / <span>3:22</span></div>
    <div class="hd">HD</div>
  </div>
</div>
<div class="abs gymnast" role="img" aria-label="Gymnast in a black leotard doing a handstand split on the beam beside score cards reading 8, 7.5 and 6.5"></div>
<p class="abs tagline">Judges only<br>give you<br>a number...</p>
<p class="abs tagline second">...We will explain<br>the reason</p>
<div class="abs cta"><div class="cta-inner"><small>Upload your video<br>&amp; get critiqued!</small><b>Get started</b></div></div>

<main>
  <div class="abs panel"></div>

  <article class="abs card" style="left:165px">
    <div class="icon" role="img" aria-label="Open box with green upload arrow"></div>
    <h3>Upload Your<br>Video</h3>
    <p>Lorem Ipsum is simply dummy text of the printing.</p>
    <div class="more">Read More</div>
  </article>
  <article class="abs card" style="left:461px">
    <div class="icon" role="img" aria-label="Two judges, a man and a woman"></div>
    <h3>We’ll judge your<br>routine</h3>
    <p>Lorem Ipsum is simply dummy text of the printing.</p>
    <div class="more">Read More</div>
  </article>
  <article class="abs card" style="left:758px">
    <div class="icon" role="img" aria-label="Scroll with a red wax seal"></div>
    <h3>Get the “why” &amp;<br>much, much more!</h3>
    <p>Lorem Ipsum is simply dummy text of the printing.</p>
    <div class="more">Read More</div>
  </article>

  <div class="abs step" style="left:167px">
    <div class="pic" role="img" aria-label="Studio microphone"></div>
    <span class="label" style="left:98px">Record your routine</span>
  </div>
  <div class="abs step" style="left:461px">
    <div class="pic" role="img" aria-label="Hard drive with yellow upload arrow" style="background:linear-gradient(#ffd640,#8aa6d8)"></div>
    <span class="label" style="left:96px">Sign up &amp; Upload</span>
  </div>
  <div class="abs step" style="left:753px">
    <span class="qmark">?</span>
    <span class="label" style="left:97px">Get the “Why”</span>
  </div>

  <h2 class="abs intro-title">Being <b>judged</b> has hever been <b>easier</b></h2>
  <p class="abs intro-copy">Le Lorem Ipsum est simplement du faux texte employé dans la composition et la mise en page avant impression. Le Lorem Ipsum est le faux texte standard de. Quand un peintre anonyme assembla ensemble des morceaux de texte pour réaliser un livre spécimen de polices de texte. Il n'a pas fait que survivre cinq siècles, mais s'est aussi adapté à la bureautique informatique, sans que son contenu n'en soit modifié.</p>
</main>

<footer class="abs site-footer"></footer>
<nav class="abs footer-nav"><a href="#">Home</a><i>|</i><a href="#">How it works</a><i>|</i><a href="#">FAQ</a><i>|</i><a href="#">Sample critique</a><i>|</i><a href="#">Member Area</a><i>|</i><a href="#">About</a></nav>
<p class="abs copyright">© Copyrights 2012 All rights Reserved</p>

</body>
</html>
```